Coral Bay Pools New website

I currently operate a swimming pool service and repair business and looking for a re design for my website as it has been over 5 years since it was designed. current site is coralbaypoolslv.com

```html
<!DOCTYPE html>
<html lang="en">
<head>
<meta charset="utf-8">
<title>Coral Bay Pools</title>
<link href="https://fonts.googleapis.com/css2?family=Poppins:wght@400;500;600;700&family=Prata&family=Great+Vibes&display=swap" rel="stylesheet">
<style>
:root{
  --blue:#1b5a96;
  --navy:#0f3e6e;
  --orange:#f5a623;
  --orange-dark:#e98f0c;
  --text:#555b63;
  --muted:#8a9099;
  --line:#e3e6ea;
  --white:#ffffff;
  --footer:#134f86;
}
*{box-sizing:border-box;margin:0;padding:0}
html,body{width:1200px;height:5364px;overflow:hidden}
body{position:relative;background:var(--white);font-family:'Poppins',sans-serif;color:var(--text)}
.abs{position:absolute}
.btn{display:inline-flex;align-items:center;justify-content:center;background:linear-gradient(180deg,#f9bb3a,var(--orange-dark));color:#3b2a07;font-weight:600;font-size:14px;letter-spacing:.5px;text-transform:uppercase;border-radius:30px;box-shadow:0 4px 10px rgba(233,143,12,.35)}
.serif{font-family:'Prata',serif}
.section-title{font-family:'Prata',serif;color:var(--blue);font-size:50px;letter-spacing:1px;text-transform:uppercase}
.rule{display:flex;align-items:center;gap:6px}
.rule span{display:block;height:2px;width:36px;background:var(--orange)}
.rule i{display:block;width:8px;height:8px;border-radius:50%;background:var(--orange)}
.center{left:0;width:1200px;text-align:center}
.center .rule{justify-content:center}

/* header */
.site-header{top:0;left:0;width:1200px;height:192px;background:var(--white)}
.brand{left:60px;top:40px;display:flex;align-items:center;gap:14px}
.brand-dot{width:56px;height:56px;border-radius:50%;background:var(--blue)}
.brand-name{font-weight:700;font-size:26px;color:var(--blue)}
.phone{left:720px;top:48px;display:flex;align-items:center;gap:12px;font-weight:700;font-size:24px;color:#222}
.phone-icon{width:40px;height:40px;border-radius:50%;background:var(--orange);display:flex;align-items:center;justify-content:center}
.header-cta{left:960px;top:46px;width:184px;height:44px}
.main-nav{right:56px;top:116px;display:flex;gap:44px;font-size:15px;font-weight:500;color:#2b3a4a}
.main-nav .active{color:var(--blue);border-bottom:2px solid var(--orange);padding-bottom:6px}

/* hero */
.hero{top:192px;left:0;width:1200px;height:676px;background:linear-gradient(180deg,#3b4a45 0%,#4e5d55 35%,#5c7f8a 62%,#2f6f8f 80%,#1f4f6a 100%)}
.hero-shade{top:192px;left:0;width:1200px;height:676px;background:rgba(10,20,30,.25)}
.hero-eyebrow{top:330px;font-size:16px;color:var(--white);letter-spacing:2px;font-weight:500}
.hero-title{top:350px;font-family:'Prata',serif;font-size:96px;color:var(--white);letter-spacing:2px}
.hero-script{top:438px;font-family:'Great Vibes',cursive;font-size:150px;color:var(--orange);line-height:1}
.hero-sub{top:598px;font-size:18px;color:var(--white);line-height:1.5}
.hero-cta{left:512px;top:684px;width:176px;height:48px}

/* features */
.feature{top:960px;width:240px;text-align:center}
.feature p{margin-top:16px;font-family:'Prata',serif;font-size:19px;color:#222;line-height:1.3}

/* about */
.about-title{left:72px;top:1372px}
.about-rule{left:72px;top:1442px}
.about-lead{left:72px;top:1470px;width:500px;font-size:22px;font-weight:700;color:#1f2630;line-height:1.45}
.about-copy{left:72px;top:1544px;width:500px;font-size:15.5px;line-height:1.75}
.about-btn{left:72px;top:1748px;width:144px;height:46px}
.hex-photo{left:620px;top:1310px}

/* services */
.services-title{top:2052px}
.services-rule{top:2120px}
.card{top:2192px;width:310px;height:470px;background:var(--white);box-shadow:0 4px 18px rgba(0,0,0,.12);text-align:center}
.card-img{margin:18px 18px 0;height:232px}
.card h3{margin-top:22px;font-family:'Prata',serif;font-weight:400;font-size:24px;color:var(--blue);text-transform:uppercase}
.card p{margin:10px 30px 0;font-size:15px;line-height:1.6}
.card .btn{margin-top:22px;width:136px;height:40px}

/* testimonials */
.testi-title{top:2776px}
.testi-rule{top:2844px}
.quote-mark{top:2920px}
.testi-text{left:290px;width:620px;top:3030px;font-size:15.5px;font-style:italic;line-height:1.75;text-align:center;color:#3b4048}
.testi-name{top:3184px;font-family:'Prata',serif;font-size:22px;color:var(--blue);letter-spacing:1px}
.stars{top:3222px}
.dots{display:flex;gap:10px;justify-content:center}
.dots b{width:9px;height:9px;border-radius:50%;background:#c7ccd2}
.dots b:first-child{background:#6b7480}

/* blog */
.blog-title{top:3376px}
.blog-rule{top:3444px}
.post{top:3500px;width:316px;height:500px;background:var(--white);box-shadow:0 4px 18px rgba(0,0,0,.12)}
.post-img{margin:20px 20px 0;height:236px}
.post-date{margin:22px 24px 0;font-size:14px;color:#3b4048;display:flex;align-items:center;gap:8px}
.post h3{margin:12px 24px 0;font-family:'Prata',serif;font-weight:400;font-size:24px;color:var(--blue)}
.post p{margin:10px 24px 0;font-size:15px;line-height:1.6}
.post .btn{margin:20px 24px 0;width:136px;height:40px}

/* contact */
.contact-title{left:72px;top:4236px}
.contact-rule{left:72px;top:4306px}
.contact-note{left:72px;top:4334px;font-size:14.5px;color:#3b4048}
.field{height:56px;border:1px solid var(--line);background:var(--white);box-shadow:0 2px 6px rgba(0,0,0,.05);font-size:14px;color:#a0a6ad;padding:18px 16px}
.submit{left:72px;top:4690px;width:180px;height:48px}

/* footer */
.site-footer{top:4872px;left:0;width:1200px;height:492px;background:linear-gradient(180deg,#1a5f9c,#0f4677)}
.footer-brand{left:72px;top:4928px;display:flex;flex-direction:column;align-items:center;gap:14px;width:240px}
.footer-brand .brand-name{color:var(--white);font-size:28px}
.footer-brand .brand-dot{width:90px;height:90px;background:var(--orange)}
.socials{display:flex;gap:12px}
.socials b{width:34px;height:34px;border-radius:50%;background:var(--white)}
.footer-col h4{font-size:26px;font-weight:600;color:var(--white);letter-spacing:1px}
.footer-col .rule{margin-top:8px}
.footer-links{list-style:none;margin-top:22px}
.footer-links li{font-size:15px;color:var(--white);margin-bottom:14px;display:flex;align-items:center;gap:10px}
.footer-links li::before{content:"";width:6px;height:6px;border-radius:50%;background:var(--white)}
.contact-row{display:flex;align-items:center;gap:16px;margin-top:20px;color:var(--white);font-size:14.5px;line-height:1.45}
.contact-row .ic{width:38px;height:38px;border-radius:50%;background:var(--white);flex:none;display:flex;align-items:center;justify-content:center}
.footer-divider{left:0;top:5272px;width:1200px;height:1px;background:rgba(255,255,255,.25)}
.copyright{top:5300px;font-size:14px;color:var(--white)}
</style>
</head>
<body>

<header class="site-header abs">
  <div class="brand abs"><span class="brand-dot"></span><span class="brand-name">Coral Bay Pools</span></div>
  <div class="phone abs">
    <span class="phone-icon"><svg width="20" height="20" viewBox="0 0 24 24"><path fill="#fff" d="M6.6 10.8a15.1 15.1 0 0 0 6.6 6.6l2.2-2.2c.3-.3.7-.4 1-.2 1.1.4 2.3.6 3.6.6.6 0 1 .4 1 1V20c0 .6-.4 1-1 1C10.6 21 3 13.4 3 4c0-.6.4-1 1-1h3.5c.6 0 1 .4 1 1 0 1.3.2 2.5.6 3.6.1.3 0 .7-.2 1z"/></svg></span>
    (702) 555-0148
  </div>
  <a class="btn header-cta abs">Contact Us</a>
  <nav class="main-nav abs">
    <span class="active">HOME</span><span>ABOUT US</span><span>OUR SERVICES</span><span>FREE ESTIMATE</span><span>OUR TESTIMONIALS</span><span>OUR BLOG</span>
  </nav>
</header>

<section>
  <div class="hero abs" role="img" aria-label="Photo of a long backyard swimming pool lined with trees at dusk"></div>
  <div class="hero-shade abs"></div>
  <div class="hero-eyebrow abs center">WELCOME TO</div>
  <h1 class="hero-title abs center" style="font-weight:400">CORAL BAY</h1>
  <div class="hero-script abs center">Pools</div>
  <p class="hero-sub abs center">The swimming pool at your facility should be properly maintained to<br>ensure your guests or residents are safe</p>
  <a class="btn hero-cta abs">Contact Us</a>
</section>

<section>
  <div class="feature abs" style="left:120px">
    <svg width="180" height="190" viewBox="0 0 180 190"><polygon points="90,4 172,50 172,140 90,186 8,140 8,50" fill="none" stroke="#9aa6b3" stroke-width="1.5"/><polygon points="90,18 158,57 158,133 90,172 22,133 22,57" fill="#f5a623"/><circle cx="90" cy="88" r="22" fill="none" stroke="#1f2630" stroke-width="3"/><path d="M79 88l8 8 15-16" fill="none" stroke="#1f2630" stroke-width="3"/><path d="M76 112l-6 18 12-4 8 8 4-16M104 112l6 18-12-4-8 8" fill="none" stroke="#1f2630" stroke-width="3"/></svg>
    <p>Quality Well<br>Results</p>
  </div>
  <div class="feature abs" style="left:360px">
    <svg width="180" height="190" viewBox="0 0 180 190"><polygon points="90,4 172,50 172,140 90,186 8,140 8,50" fill="none" stroke="#9aa6b3" stroke-width="1.5"/><polygon points="90,18 158,57 158,133 90,172 22,133 22,57" fill="#f5a623"/><circle cx="90" cy="78" r="16" fill="none" stroke="#1f2630" stroke-width="3"/><path d="M60 126c0-18 13-28 30-28s30 10 30 28z" fill="none" stroke="#1f2630" stroke-width="3"/></svg>
    <p>Professional &amp;<br>Trusted Staff</p>
  </div>
  <div class="feature abs" style="left:600px">
    <svg width="180" height="190" viewBox="0 0 180 190"><polygon points="90,4 172,50 172,140 90,186 8,140 8,50" fill="none" stroke="#9aa6b3" stroke-width="1.5"/><polygon points="90,18 158,57 158,133 90,172 22,133 22,57" fill="#f5a623"/><circle cx="90" cy="95" r="24" fill="none" stroke="#1f2630" stroke-width="8" stroke-dasharray="8 5"/><circle cx="90" cy="95" r="10" fill="none" stroke="#1f2630" stroke-width="3"/></svg>
    <p>Committed To<br>Success</p>
  </div>
  <div class="feature abs" style="left:840px">
    <svg width="180" height="190" viewBox="0 0 180 190"><polygon points="90,4 172,50 172,140 90,186 8,140 8,50" fill="none" stroke="#9aa6b3" stroke-width="1.5"/><polygon points="90,18 158,57 158,133 90,172 22,133 22,57" fill="#f5a623"/><g fill="none" stroke="#1f2630" stroke-width="2.5"><polygon points="90,62 95,73 107,74 98,82 101,94 90,88 79,94 82,82 73,74 85,73"/><polygon points="62,78 66,86 74,87 68,92 70,100 62,96 55,100 57,92 51,87 59,86"/><polygon points="118,78 122,86 130,87 124,92 126,100 118,96 111,100 113,92 107,87 115,86"/><circle cx="90" cy="112" r="7"/><path d="M74 134c0-9 7-14 16-14s16 5 16 14"/></g></svg>
    <p>100% Clients<br>Satisfied</p>
  </div>
</section>

<section>
  <h2 class="section-title about-title abs" style="font-weight:400">About Us</h2>
  <div class="rule about-rule abs"><span></span><i></i><span></span></div>
  <p class="about-lead abs">We are a full service pool company servicing the Las Vegas Valley.</p>
  <p class="about-copy abs">My name is Daniel and I'm the owner of Coral Bay Pools. I recently started this business in 2018 to provide Las Vegas with excellent, reliable pool service. Just because we are a new company that doesn't mean we lack experience. I've been in the pool industry for seven years and counting and have managed everything from your backyard pool to olympic sized pools with five plus years managing casino properties as well.</p>
  <a class="btn about-btn abs">Read More</a>
  <svg class="hex-photo abs" width="540" height="580" viewBox="0 0 540 580">
    <defs><linearGradient id="aboutG" x1="0" y1="0" x2="0" y2="1"><stop offset="0" stop-color="#e9eef2"/><stop offset=".45" stop-color="#9fb7a6"/><stop offset=".7" stop-color="#39a6c9"/><stop offset="1" stop-color="#6b5a48"/></linearGradient></defs>
    <polygon points="270,6 528,150 528,430 270,574 12,430 12,150" fill="none" stroke="#f5a623" stroke-width="2.5"/>
    <polygon points="270,30 504,162 504,418 270,550 36,418 36,162" fill="url(#aboutG)" role="img" aria-label="Photo of a white villa with a blue pool and wooden deck"/>
  </svg>
</section>

<section>
  <h2 class="section-title services-title abs center" style="font-weight:400">Our Services</h2>
  <div class="rule services-rule abs center"><span></span><i></i><span></span></div>
  <article class="card abs" style="left:72px">
    <div class="card-img" role="img" aria-label="Photo of a pool skimmer net in bright blue water" style="background:linear-gradient(135deg,#7fd3f2,#1a8fd0)"></div>
    <h3>Pool Services</h3>
    <p>When you invested in your pool you knew it was a long-term investment in both money and time. At home, it's an oasis...</p>
    <a class="btn">Read More</a>
  </article>
  <article class="card abs" style="left:445px">
    <div class="card-img" role="img" aria-label="Photo of a rooftop commercial pool among city towers" style="background:linear-gradient(180deg,#c9d2da,#7c8c99 60%,#4f9fc0)"></div>
    <h3>Commercial Pools</h3>
    <p>As a commercial property owner or manager, doing your job well requires you to be mindful of all the details...</p>
    <a class="btn">Read More</a>
  </article>
  <article class="card abs" style="left:818px">
    <div class="card-img" role="img" aria-label="Photo of a residential pool beside a house at sunset" style="background:linear-gradient(180deg,#7a6a55,#5a7f8c 55%,#2f93b8)"></div>
    <h3>Residential Pools</h3>
    <p>Here in Southern Nevada, you know it can get really, really hot. That's why you invested in your pool at home...</p>
    <a class="btn">Read More</a>
  </article>
</section>

<section>
  <h2 class="section-title testi-title abs center" style="font-weight:400">Our Testimonials</h2>
  <div class="rule testi-rule abs center"><span></span><i></i><span></span></div>
  <div class="quote-mark abs center"><svg width="96" height="80" viewBox="0 0 96 80"><path fill="#f5a623" d="M0 80V44C0 18 12 4 36 0l4 10C26 14 20 24 20 36h18v44zM54 80V44C54 18 66 4 90 0l4 10C80 14 74 24 74 36h18v44z"/></svg></div>
  <p class="testi-text abs">Lorem ipsum dolor sit amet, consectetur adipiscing elit, sed do eiusmod tempor incididunt ut labore et dolore magna aliqua. Ut enim ad minim veniam, quis nostrud exercitation ullamco laboris nisi ut aliquip ex ea commodo consequat. Duis aute irure dolor in reprehenderit in voluptate.</p>
  <div class="testi-name abs center">MARCUS REED</div>
  <div class="stars abs center"><svg width="150" height="24" viewBox="0 0 150 24"><g fill="#f5a623"><polygon id="st" points="12,1 15,9 23,9 17,14 19,22 12,17 5,22 7,14 1,9 9,9"/><use href="#st" x="31"/><use href="#st" x="62"/><use href="#st" x="93"/><use href="#st" x="124"/></g></svg></div>
  <div class="dots abs center" style="top:3282px"><b></b><b></b><b></b><b></b></div>
</section>

<section>
  <h2 class="section-title blog-title abs center" style="font-weight:400">Our Blog</h2>
  <div class="rule blog-rule abs center"><span></span><i></i><span></span></div>
  <article class="post abs" style="left:72px">
    <div class="post-img" role="img" aria-label="Photo of a backyard pool with stone patio" style="background:linear-gradient(180deg,#d9dde0,#8fb0a8 55%,#3aa4cf)"></div>
    <div class="post-date"><svg width="16" height="16" viewBox="0 0 16 16"><rect x="1" y="3" width="14" height="12" rx="1" fill="none" stroke="#f5a623" stroke-width="1.6"/><path d="M1 7h14M5 1v4M11 1v4" stroke="#f5a623" stroke-width="1.6"/></svg>January 13, 2026</div>
    <h3>Lorem ipsum dolor sit amet</h3>
    <p>Sed ut perspiciatis unde omnis iste natus error sit voluptatem accusan tium doloremque laudantium,...</p>
    <a class="btn">Read More</a>
  </article>
  <article class="post abs" style="left:442px">
    <div class="post-img" role="img" aria-label="Photo of a modern house with an evening lit pool" style="background:linear-gradient(180deg,#b8c2cc,#6f7c88 55%,#2f8fc0)"></div>
    <div class="post-date"><svg width="16" height="16" viewBox="0 0 16 16"><rect x="1" y="3" width="14" height="12" rx="1" fill="none" stroke="#f5a623" stroke-width="1.6"/><path d="M1 7h14M5 1v4M11 1v4" stroke="#f5a623" stroke-width="1.6"/></svg>January 13, 2026</div>
    <h3>Lorem ipsum dolor sit amet</h3>
    <p>Sed ut perspiciatis unde omnis iste natus error sit voluptatem accusan tium doloremque laudantium,...</p>
    <a class="btn">Read More</a>
  </article>
  <article class="post abs" style="left:812px">
    <div class="post-img" role="img" aria-label="Photo of a resort pool framed by palm trees" style="background:linear-gradient(180deg,#9cc7e6,#6ea27a 50%,#2b9ccc)"></div>
    <div class="post-date"><svg width="16" height="16" viewBox="0 0 16 16"><rect x="1" y="3" width="14" height="12" rx="1" fill="none" stroke="#f5a623" stroke-width="1.6"/><path d="M1 7h14M5 1v4M11 1v4" stroke="#f5a623" stroke-width="1.6"/></svg>January 13, 2026</div>
    <h3>Lorem ipsum dolor sit amet</h3>
    <p>Sed ut perspiciatis unde omnis iste natus error sit voluptatem accusan tium doloremque laudantium,...</p>
    <a class="btn">Read More</a>
  </article>
  <div class="dots abs center" style="top:4096px"><b></b><b></b><b></b><b></b></div>
</section>

<section>
  <h2 class="section-title contact-title abs" style="font-weight:400">Contact Us</h2>
  <div class="rule contact-rule abs"><span></span><i></i><span></span></div>
  <p class="contact-note abs">For more information please fill out the following and we will be in touch shortly</p>
  <div class="field abs" style="left:72px;top:4392px;width:264px">First Name</div>
  <div class="field abs" style="left:356px;top:4392px;width:264px">Second Name</div>
  <div class="field abs" style="left:72px;top:4472px;width:264px">Phone</div>
  <div class="field abs" style="left:356px;top:4472px;width:264px">Subject</div>
  <div class="field abs" style="left:72px;top:4552px;width:548px;height:110px">Message</div>
  <a class="btn submit abs">Submit a Message</a>
  <svg class="abs" style="left:680px;top:4190px" width="480" height="520" viewBox="0 0 480 520">
    <defs><linearGradient id="contactG" x1="0" y1="0" x2="0" y2="1"><stop offset="0" stop-color="#cfe3ef"/><stop offset=".45" stop-color="#5f9a62"/><stop offset=".7" stop-color="#2fa6cf"/><stop offset="1" stop-color="#1f7fa8"/></linearGradient></defs>
    <polygon points="240,6 470,134 470,386 240,514 10,386 10,134" fill="none" stroke="#f5a623" stroke-width="2.5"/>
    <polygon points="240,28 450,146 450,374 240,492 30,374 30,146" fill="url(#contactG)" role="img" aria-label="Photo of a tropical pool with palm trees and lounge chairs"/>
  </svg>
</section>

<footer>
  <div class="site-footer abs" role="img" aria-label="Faint blue photo of pool water behind the footer"></div>
  <div class="footer-brand abs">
    <span class="brand-dot"></span>
    <span class="brand-name">Coral Bay Pools</span>
    <div class="socials"><b></b><b></b><b></b></div>
  </div>
  <div class="footer-col abs" style="left:470px;top:4924px">
    <h4>LINKS</h4>
    <div class="rule"><span></span><i></i></div>
    <ul class="footer-links">
      <li>About Us</li><li>Our Services</li><li>Our Testimonials</li><li>Our Blog</li><li>Contact Us</li>
    </ul>
  </div>
  <div class="footer-col abs" style="left:790px;top:4924px;width:360px">
    <h4>CONTACT</h4>
    <div class="rule"><span></span><i></i></div>
    <div class="contact-row"><span class="ic"><svg width="16" height="18" viewBox="0 0 16 20"><path fill="#134f86" d="M8 0a7 7 0 0 0-7 7c0 5 7 13 7 13s7-8 7-13a7 7 0 0 0-7-7zm0 10a3 3 0 1 1 0-6 3 3 0 0 1 0 6z"/></svg></span><span>Serving the Las Vegas Valley,<br>Nevada</span></div>
    <div class="contact-row"><span class="ic"><svg width="16" height="16" viewBox="0 0 24 24"><path fill="#134f86" d="M6.6 10.8a15.1 15.1 0 0 0 6.6 6.6l2.2-2.2c.3-.3.7-.4 1-.2 1.1.4 2.3.6 3.6.6.6 0 1 .4 1 1V20c0 .6-.4 1-1 1C10.6 21 3 13.4 3 4c0-.6.4-1 1-1h3.5c.6 0 1 .4 1 1 0 1.3.2 2.5.6 3.6.1.3 0 .7-.2 1z"/></svg></span><span>(702) 555-0148</span></div>
    <div class="contact-row"><span class="ic"><svg width="16" height="14" viewBox="0 0 20 16"><rect x="1" y="1" width="18" height="14" rx="1.5" fill="none" stroke="#134f86" stroke-width="2"/><path d="M1 2l9 7 9-7" fill="none" stroke="#134f86" stroke-width="2"/></svg></span><span>service@coralbaypoolslv.com</span></div>
  </div>
  <div class="footer-divider abs"></div>
  <div class="copyright abs center">©2026 Coral Bay Pools - Do not copy. All rights reserved.</div>
</footer>

</body>
</html>
```